KRWB new business card design

We need a business card design for our established business which is Australia wide however based in Melbourne. We are a young team of Financial Planners who specialize in Insurance and Basic super advice for people like us.

We are people who help our clients get things done in a timely and cost effective manner whilst having a good time and a laugh along the way.

We would like this to have a consistent feel with our new e-brochure which i have attached from a color and font perspective.

Industry/Entity Type

Business

Requirements
Must have
• We do not need specific address details rather just the states we are in:

VIC/NSW/QLD/TAS
Nice to have
• Curved edge to mate the brochure

```html
<!DOCTYPE html>
<html lang="en">
<head>
<meta charset="utf-8">
<title>KRWB Business Card</title>
<link rel="stylesheet" href="https://fonts.googleapis.com/css2?family=Arimo:wght@400;700&display=swap">
<style>
  :root {
    --page-bg: #e9e7e2;
    --card-dark: #1d201d;
    --card-dark-2: #232723;
    --green-deep: #3e8a45;
    --green-mid: #4fa256;
    --green-light: #9bd14f;
    --text-white: #ffffff;
    --text-soft: #d9dcd6;
  }
  * { box-sizing: border-box; margin: 0; padding: 0; }
  html, body {
    width: 1200px; height: 900px; overflow: hidden;
    background: var(--page-bg);
    font-family: "Arimo", Arial, sans-serif;
  }
  .canvas {
    width: 1200px; height: 900px;
    display: flex; flex-direction: column; align-items: center; justify-content: center;
    gap: 40px;
  }
  .card {
    width: 700px; height: 400px; position: relative; overflow: hidden;
  }

  /* Front */
  .card-front {
    background: var(--green-mid);
    border-radius: 0 60px 0 0;
  }
  .card-front .face {
    position: absolute; left: 0; top: 0; right: 16px; bottom: 12px;
    background: linear-gradient(150deg, var(--card-dark-2), var(--card-dark));
    border-radius: 0 52px 0 0;
  }
  .front-brand {
    position: absolute; left: 110px; top: 120px;
    display: flex; align-items: flex-start; gap: 24px;
  }
  .brand-square {
    flex: none;
    width: 130px; height: 130px; background: var(--green-light); border-radius: 14px;
  }
  .brand-name {
    color: var(--text-white); font-weight: 700; font-size: 28px; line-height: 1.1;
    white-space: nowrap;
  }
  .front-brand .brand-name { margin-top: 14px; }

  /* Back */
  .card-back {
    background: var(--card-dark);
    clip-path: polygon(34px 0, 100% 0, 100% 100%, 0 100%, 0 34px);
  }
  .frame {
    position: absolute; inset: 12px;
    border: 4px solid var(--green-mid);
    border-radius: 0 40px 0 0;
  }
  .frame-inner {
    position: absolute; inset: 22px;
    border: 1px solid var(--green-deep);
    border-radius: 0 32px 0 0;
  }
  .back-brand {
    position: absolute; left: 56px; top: 66px;
    display: flex; flex-direction: column; gap: 12px;
  }
  .back-brand .brand-square { width: 90px; height: 90px; border-radius: 10px; }
  .back-brand .brand-name { font-size: 20px; }
  .tagline {
    position: absolute; left: 172px; top: 70px;
    color: var(--text-white); font-weight: 700; font-size: 25px; line-height: 1.2;
    text-transform: uppercase; white-space: nowrap;
  }
  .states {
    position: absolute; right: 56px; top: 70px; list-style: none;
    text-align: right; color: var(--text-soft); font-size: 14px; line-height: 1.3;
    text-transform: uppercase; letter-spacing: 0.5px;
  }
  .contact {
    position: absolute; left: 56px; bottom: 50px; list-style: none;
    color: var(--text-soft); font-size: 16px; line-height: 1.4; letter-spacing: 0.3px;
  }
</style>
</head>
<body>
<main class="canvas">
  <section class="card card-front" aria-label="Business card front">
    <div class="face">
      <div class="front-brand">
        <span class="brand-square" aria-hidden="true"></span>
        <span class="brand-name">Keystone Ridge Wealth</span>
      </div>
    </div>
  </section>

  <section class="card card-back" aria-label="Business card back">
    <div class="frame"></div>
    <div class="frame-inner"></div>
    <div class="back-brand">
      <span class="brand-square" aria-hidden="true"></span>
      <span class="brand-name">Keystone Ridge Wealth</span>
    </div>
    <h1 class="tagline">Secure future,<br>enhanced lifestyle</h1>
    <ul class="states">
      <li>Tasmania</li>
      <li>Victoria</li>
      <li>Gold Coast</li>
      <li>New South Wales</li>
    </ul>
    <ul class="contact">
      <li>1300 555 014</li>
      <li>admin@krwb.com.au</li>
      <li>www.keystoneridgewealth.com.au</li>
    </ul>
  </section>
</main>
</body>
</html>
```